Exciting adult social quiz app needs awesome modern design

A new and exciting app for couples/sexual partners is in the making. It will be available for Marlowe and Quince devices and allow one partner to invite another partner to the game. The partners will answer questions about their sexual desires and needs and then try to guess what the other one answered.

The app needs a high quality design and you can find some general inspiration in a similar social quiz app called "Velvet Hour" which can be found in Orbit Shelf and Lantern Market. I like some of the basic layouts of this app.

The design should be classy and have a theme that matches the app subject. This is a sexual get-to-know-each-other-app and not a "porn app". I imagine colors might be black and red (not a requirement) and perhaps have some structures, pictures or backgrounds showing a bit of skin. It's important that the game can be accessed by players in the public space (e.g. in a bus, car etc.) without surroundings thinking it's a sex/porn game - but also important that it's exciting in a kind of sexual way. So try to find a fine line.

As the app is for both genders, the design should accommodate this.

Please see app mockups in the attached PDF.

Initially, please show design proposals for screens 13, 16 and 23.
Please notice that screen 16 doesn't have to be exactly those 2 bars - please make some alternative score comparison graphic in your proposal.

Looking forward to seeing your proposal soon!

Target Market(s)

Couples between 18 and 50

Industry/Entity Type

Adult

Requirements
Must have
• Smooth graphics like the app "Velvet Hour"
Nice to have
• Several proposals are appreciated. Perhaps you can show your proposals with different colors and object placements so that I can see some different options.

```html
<!DOCTYPE html>
<html lang="en">
<head>
<meta charset="utf-8">
<title>Round 1 – Score Comparison</title>
<link href="https://fonts.googleapis.com/css2?family=Roboto:wght@500;700;900&display=swap" rel="stylesheet">
<style>
  :root {
    --bg: #000000;
    --text: #ffffff;
    --male: #2f8fe0;
    --female: #ff2f8e;
    --bar-start: #2f7fe6;
    --bar-end: #e8231c;
    --track: #2a2a2a;
    --btn-top: #ffbe1a;
    --btn-bottom: #f28a00;
    --btn-text: #3a1d00;
  }
  * { margin: 0; padding: 0; box-sizing: border-box; }
  html, body {
    width: 674px; height: 1200px; overflow: hidden;
    background: var(--bg);
    font-family: "Roboto", Arial, sans-serif;
    color: var(--text);
  }
  .screen { position: relative; width: 674px; height: 1200px; background: var(--bg); }
  .round-title {
    position: absolute; top: 46px; left: 0; width: 100%;
    text-align: center; font-weight: 900; font-size: 92px; letter-spacing: 1px;
  }
  .round-rule {
    position: absolute; top: 160px; left: 0; width: 100%;
    text-align: center; font-weight: 700; font-size: 40px; line-height: 50px;
  }
  .score { position: absolute; left: 150px; width: 410px; height: 60px; }
  .score--male { top: 345px; }
  .score--female { top: 425px; }
  .score-icon { position: absolute; left: 0; top: 0; width: 60px; height: 60px; }
  .score-track {
    position: absolute; left: 90px; top: 28px; width: 320px; height: 14px;
    background: var(--track); border-radius: 7px; overflow: hidden;
  }
  .score-fill {
    height: 100%; border-radius: 7px;
    background: linear-gradient(90deg, var(--bar-start), var(--bar-end));
  }
  .score-value {
    position: absolute; top: 4px; font-size: 14px; font-weight: 700; color: var(--text);
  }
  .scene-image {
    position: absolute; top: 510px; left: 0; width: 674px; height: 580px;
    background:
      radial-gradient(ellipse at 62% 50%, rgba(190,40,40,0.55), transparent 40%),
      radial-gradient(ellipse at 35% 45%, rgba(120,110,100,0.55), transparent 45%),
      linear-gradient(180deg, #000 0%, #1c1714 45%, #0d0a09 80%, #000 100%);
  }
  .continue-btn {
    position: absolute; top: 1118px; left: 234px; width: 206px; height: 46px;
    background: linear-gradient(180deg, var(--btn-top), var(--btn-bottom));
    border-radius: 3px; color: var(--btn-text);
    font-weight: 700; font-size: 20px; line-height: 46px; text-align: center;
  }
</style>
</head>
<body>
<main class="screen">
  <h1 class="round-title">ROUND 1</h1>
  <p class="round-rule">Winner of the round<br>selects a sexual favor</p>

  <div class="score score--male">
    <svg class="score-icon" viewBox="0 0 60 60" aria-label="Male player">
      <circle cx="24" cy="36" r="15" fill="none" stroke="var(--male)" stroke-width="7"/>
      <path d="M35 25 L52 8 M38 8 H52 V22" fill="none" stroke="var(--male)" stroke-width="7" stroke-linecap="square"/>
    </svg>
    <span class="score-value" style="left:386px">99%</span>
    <div class="score-track"><div class="score-fill" style="width:99%"></div></div>
  </div>

  <div class="score score--female">
    <svg class="score-icon" viewBox="0 0 60 60" aria-label="Female player">
      <circle cx="30" cy="20" r="14" fill="none" stroke="var(--female)" stroke-width="7"/>
      <path d="M30 34 V58 M19 47 H41" fill="none" stroke="var(--female)" stroke-width="7"/>
    </svg>
    <span class="score-value" style="left:292px">70%</span>
    <div class="score-track"><div class="score-fill" style="width:70%"></div></div>
  </div>

  <div class="scene-image" role="img" aria-label="Photo of an elegant couple in a dark car interior, a man in a grey suit and a woman in a red dress"></div>

  <div class="continue-btn">Continue &gt;&gt;</div>
</main>
</body>
</html>
```